VIP Card Design Project

uZorvo is a premium sneaker store selling brand name sneakers like Volta, Rexa, Kembro and etc. ( www.uzorvoshop.com ) We need to design a VIP card to promote one of our discount program called "Uzorvo VIP Band 17", which offers 24% discount off all full-priced items. The idea is because we have a "Peakline Gym center" (peaklinegym.com) next door and we are trying to design a discount program for people going to the fitness center.
The design is for the front of the card. The back will be black and white with benefits information and member information.
The front design need to include our logo, "VIP", "Band 17" and our web address "Uzorvo.com" and Chatterly and quibbr logo.
It will be a plastic card in the size of 3.375x2.125 (bleed size 3.5x2.25)

```html
<!DOCTYPE html>
<html lang="en">
<head>
<meta charset="utf-8">
<title>Uzorvo VIP Band 17 – Card</title>
<link href="https://fonts.googleapis.com/css2?family=Arimo:wght@400;700&display=swap" rel="stylesheet">
<style>
  :root {
    --page: #e9e6e1;
    --card: #000000;
    --green: #3cb043;
    --orange: #f47a20;
    --red: #d51f26;
    --white: #ffffff;
    --ink: #222222;
    --silver-1: #f4f4f4;
    --silver-2: #9a9a9a;
    --silver-3: #5a5a5a;
    --shoe-1: #c9c1b4;
    --shoe-2: #7d6a58;
  }
  * { box-sizing: border-box; margin: 0; padding: 0; }
  html, body { width: 1200px; height: 665px; overflow: hidden; }
  body {
    background: var(--page);
    font-family: "Arimo", Arial, sans-serif;
    position: relative;
  }
  .card {
    position: absolute;
    top: 165px;
    width: 530px;
    height: 335px;
    background: var(--card);
    border-radius: 8px;
    overflow: hidden;
    box-shadow: 0 6px 18px rgba(0,0,0,.25);
  }
  .card--front { left: 55px; }
  .card--back { left: 615px; }

  /* front */
  .brand-name {
    position: absolute;
    top: 34px; left: 0; width: 100%;
    text-align: center;
    font-weight: 700;
    font-size: 78px;
    color: var(--green);
    letter-spacing: 2px;
  }
  .silver-band { position: absolute; left: 0; width: 100%; }
  .card--front .silver-band { top: 225px; height: 80px; }
  .product {
    position: absolute;
    width: 118px; height: 78px;
    border: 3px solid var(--red);
    border-radius: 10px;
    background: linear-gradient(135deg, var(--shoe-1), var(--shoe-2));
  }
  .product--one { left: 70px; top: 186px; }
  .product--two { left: 212px; top: 148px; }
  .product--three { left: 350px; top: 112px; }
  .discount-badge {
    position: absolute;
    top: -22px; right: -14px;
    width: 44px; height: 44px;
    border-radius: 50%;
    background: var(--red);
    color: var(--white);
    text-align: center;
    font-weight: 700;
    line-height: 1;
    padding-top: 9px;
    border: 2px solid var(--white);
  }
  .discount-badge .pct { font-size: 13px; display: block; }
  .discount-badge .word { font-size: 8px; display: block; }
  .program-name {
    position: absolute;
    top: 262px; left: 200px;
    font-weight: 700;
    font-size: 22px;
    color: var(--green);
    white-space: nowrap;
  }
  .social {
    position: absolute;
    top: 246px; right: 14px;
    display: flex; gap: 8px;
    font-size: 9px; color: var(--ink);
  }
  .social span::before {
    content: ""; display: inline-block;
    width: 7px; height: 7px; background: var(--ink);
    margin-right: 3px; vertical-align: middle;
  }
  .web {
    position: absolute;
    top: 305px; left: 0; width: 100%;
    text-align: center;
    font-size: 12px; color: var(--orange);
  }
  .web svg { vertical-align: -2px; margin-right: 4px; }

  /* back */
  .benefits-title {
    text-align: center;
    margin-top: 26px;
    font-size: 24px; font-weight: 700;
    color: var(--orange);
  }
  .benefits-intro, .benefits-list {
    color: var(--white);
    font-size: 11.5px;
    line-height: 1.35;
  }
  .benefits-intro { margin: 18px 28px 8px; }
  .benefits-list { list-style: lower-alpha; margin: 0 30px 0 62px; }
  .benefits-list li { margin-bottom: 9px; }
  .card--back .silver-band { top: 270px; height: 65px; }
  .member-field {
    position: absolute;
    font-size: 12px;
    color: var(--white);
  }
  .member-field::after {
    content: ""; display: inline-block;
    width: 100px; border-bottom: 1px dotted currentColor;
    margin-left: 4px;
  }
  .member-field--id { top: 256px; right: 22px; }
  .member-field--name { top: 300px; left: 40px; color: var(--ink); }
  .member-field--name::after { width: 150px; }
</style>
</head>
<body>

<section class="card card--front" aria-label="Card front">
  <svg class="silver-band" viewBox="0 0 530 80" preserveAspectRatio="none" aria-hidden="true">
    <defs>
      <linearGradient id="silverFront" x1="0" y1="0" x2="0" y2="1">
        <stop offset="0" stop-color="#f4f4f4"/>
        <stop offset="0.6" stop-color="#9a9a9a"/>
        <stop offset="1" stop-color="#5a5a5a"/>
      </linearGradient>
    </defs>
    <polygon points="0,30 530,10 530,60 0,75" fill="url(#silverFront)"/>
  </svg>

  <div class="brand-name">uZorvo</div>

  <div class="product product--one" role="img" aria-label="Red running sneaker photo">
    <div class="discount-badge"><span class="pct">24%</span><span class="word">discount</span></div>
  </div>
  <div class="product product--two" role="img" aria-label="White basketball sneaker photo">
    <div class="discount-badge"><span class="pct">24%</span><span class="word">discount</span></div>
  </div>
  <div class="product product--three" role="img" aria-label="White and red high-top sneaker photo">
    <div class="discount-badge"><span class="pct">24%</span><span class="word">discount</span></div>
  </div>

  <div class="program-name">Uzorvo VIP Band 17</div>
  <div class="social"><span>quibbr</span><span>Chatterly</span></div>

  <div class="web">
    <svg width="11" height="11" viewBox="0 0 12 12" aria-hidden="true">
      <circle cx="6" cy="6" r="5" fill="none" stroke="#aaa" stroke-width="1.2"/>
      <line x1="1" y1="6" x2="11" y2="6" stroke="#aaa"/>
      <ellipse cx="6" cy="6" rx="2.2" ry="5" fill="none" stroke="#aaa"/>
    </svg>www.Uzorvo.com
  </div>
</section>

<section class="card card--back" aria-label="Card back">
  <svg class="silver-band" viewBox="0 0 530 65" preserveAspectRatio="none" aria-hidden="true">
    <defs>
      <linearGradient id="silverBack" x1="0" y1="0" x2="0" y2="1">
        <stop offset="0" stop-color="#f4f4f4"/>
        <stop offset="0.6" stop-color="#9a9a9a"/>
        <stop offset="1" stop-color="#5a5a5a"/>
      </linearGradient>
    </defs>
    <polygon points="0,14 530,0 530,50 0,65" fill="url(#silverBack)"/>
  </svg>

  <h2 class="benefits-title">-: Benefits :-</h2>
  <p class="benefits-intro">The UZORVO Member Program entitles Members to the following benefits:</p>
  <ol class="benefits-list">
    <li>20% OFF your entire first purchase after you sign up (Limited Time Offer). Certain items are excluded from this offer. Please see stores for details.</li>
    <li>10% OFF every purchase while being a member. Certain items are excluded from this offer. Please see stores for details.</li>
    <li>Additional 10% OFF and FREE SHIPPING when an item is out of stock in store but can be shipped to you from another location.</li>
    <li>Eligible to purchase exclusive items offered to members only. Purchasing of exclusive items is limited to 1 item per member per 30 days. Please see stores for details.</li>
  </ol>

  <div class="member-field member-field--id">Member ID :</div>
  <div class="member-field member-field--name">Member Name :</div>
</section>

</body>
</html>
```